The most modern business card ever !!!

Our company call “Vendalo”. Vendalo is a technology company specialized in cruises solutions. Out main product is a platform to reserve cruises. This is a revolutionary platform that make easier to travel agencies and final users to reserve cruises across dozen companies like tibba, wernu, hpv, dgb, etc..We are a “start up”, with a young team of developers and we want to transmit it.. For it, we want something different, a modern business card that represent cruises and technology.. When someone receive this card, this person should say: wowww this is different… this is modern… this is a cruise related company..
- diferent, modern
- traditions business card

```html
<!DOCTYPE html>
<html lang="en">
<head>
<meta charset="utf-8">
<title>Vendalo – Business Card</title>
<link rel="stylesheet" href="https://fonts.googleapis.com/css2?family=Exo+2:wght@600;700&family=Open+Sans:wght@400&display=swap">
<style>
  :root {
    --page-bg: #e4e5e7;
    --card-bg: #f8f8f8;
    --ink: #111111;
    --text: #1d1d1d;
    --accent: #27a9e1;
    --band-dark: #050505;
  }
  * { margin: 0; padding: 0; box-sizing: border-box; }
  html, body {
    width: 1200px; height: 900px; overflow: hidden;
    background: var(--page-bg);
  }
  .business-card {
    position: absolute; left: 120px; top: 153px;
    width: 960px; height: 594px;
    background: var(--card-bg);
    box-shadow: 0 18px 40px rgba(0,0,0,0.14);
    overflow: hidden;
  }
  .brand-name {
    position: absolute; left: 68px; top: 262px;
    font-family: "Exo 2", sans-serif; font-weight: 600;
    font-size: 82px; line-height: 1; letter-spacing: 1px;
    color: var(--ink);
  }
  .divider {
    position: absolute; left: 487px; top: 150px;
    width: 2px; height: 295px; background: var(--accent);
  }
  .contact-block {
    position: absolute; left: 518px; top: 140px;
    font-family: "Open Sans", sans-serif; color: var(--text);
  }
  .person-name {
    font-family: "Exo 2", sans-serif; font-weight: 700;
    font-size: 32px; line-height: 36px; letter-spacing: 0.5px;
    color: var(--accent);
  }
  .person-role { font-size: 28px; line-height: 34px; margin-bottom: 14px; }
  .contact-list { list-style: none; }
  .contact-list li {
    display: flex; align-items: center; gap: 8px;
    font-size: 28px; line-height: 35px;
  }
  .contact-list svg { width: 20px; height: 20px; flex: none; fill: var(--accent); }
  .address { font-size: 28px; line-height: 34px; margin-top: 14px; padding-left: 4px; }
  .bottom-bands { position: absolute; left: 0; bottom: 0; width: 960px; height: 40px; }
</style>
</head>
<body>
  <div class="business-card">
    <div class="brand-name">Vendalo</div>
    <div class="divider"></div>
    <div class="contact-block">
      <div class="person-name">MARCUS HALE</div>
      <div class="person-role">Managing Director</div>
      <ul class="contact-list">
        <li>
          <svg viewBox="0 0 20 20" aria-hidden="true"><path d="M2 7c0-2 3-4 8-4s8 2 8 4v2h-4V7H6v2H2z"/><path d="M5 10h10l2 7H3z"/></svg>
          055-210 384 617
        </li>
        <li>
          <svg viewBox="0 0 20 20" aria-hidden="true"><path d="M6 1h8a1 1 0 0 1 1 1v16a1 1 0 0 1-1 1H6a1 1 0 0 1-1-1V2a1 1 0 0 1 1-1zm1 3v11h6V4z"/></svg>
          055-210 384 617
        </li>
        <li>
          <svg viewBox="0 0 20 20" aria-hidden="true"><path d="M2 5h16v10H2z"/><path d="M2 5l8 6 8-6" fill="none" stroke="#f8f8f8" stroke-width="1.6"/></svg>
          hello@vendalo.io
        </li>
        <li>
          <svg viewBox="0 0 20 20" aria-hidden="true"><circle cx="10" cy="10" r="8"/><path d="M2 10h16M10 2c-3 3-3 13 0 16M10 2c3 3 3 13 0 16" fill="none" stroke="#f8f8f8" stroke-width="1.2"/></svg>
          www.vendalo.io
        </li>
      </ul>
      <div class="address">27, Quayside Road North<br>Marisport, 204518</div>
    </div>
    <svg class="bottom-bands" viewBox="0 0 960 40" aria-hidden="true">
      <polygon points="0,0 459,0 488,40 0,40" fill="var(--accent)"/>
      <polygon points="467,8 960,8 960,40 493,40" fill="var(--band-dark)"/>
    </svg>
  </div>
</body>
</html>
```